Dovetree baby skincare

design business cards (double sided) and complimentary note (single sided)

Industry/Entity Type

Business

Colors

Designer to choose colors to be used in the design.

```html
<!DOCTYPE html>
<html lang="en">
<head>
<meta charset="utf-8">
<title>Dovetree baby skincare – With Compliments slip</title>
<link rel="stylesheet" href="https://fonts.googleapis.com/css2?family=Playfair+Display:wght@700&family=Satisfy&display=swap">
<style>
  :root {
    --backdrop: #e9e6e2;
    --paper: #ffffff;
    --gold: #c9a227;
    --apricot: #f7bf73;
    --apricot-light: #fbd9a8;
    --peach: #f3c3a4;
    --peach-soft: #fae3d3;
    --ink: #1f1f1f;
    --script: #efb070;
    --script-shadow: rgba(90, 60, 30, 0.35);
  }
  * { box-sizing: border-box; margin: 0; padding: 0; }
  html, body {
    width: 1200px;
    height: 842px;
    overflow: hidden;
    background: var(--backdrop);
  }
  .canvas {
    position: relative;
    width: 1200px;
    height: 842px;
  }
  .compliment-slip {
    position: absolute;
    left: 50px;
    top: 161px;
    width: 1100px;
    height: 520px;
    background: var(--paper);
    overflow: hidden;
    box-shadow: 0 6px 24px rgba(0, 0, 0, 0.12);
  }
  .watercolour-wash {
    position: absolute;
    left: 640px;
    top: 20px;
    width: 420px;
    height: 330px;
    border-radius: 46% 54% 40% 60% / 48% 38% 62% 52%;
    background: radial-gradient(ellipse at 40% 60%, var(--peach) 0%, var(--peach-soft) 60%, rgba(250, 227, 211, 0) 100%);
    transform: rotate(-18deg);
    opacity: 0.9;
  }
  .brand-name {
    position: absolute;
    left: 58px;
    top: 126px;
    font-family: "Playfair Display", Georgia, serif;
    font-weight: 700;
    font-size: 78px;
    letter-spacing: 1px;
    color: var(--gold);
    line-height: 1;
  }
  .slip-title {
    position: absolute;
    left: 320px;
    top: 190px;
    font-family: "Satisfy", cursive;
    font-size: 92px;
    color: var(--script);
    text-shadow: 2px 3px 3px var(--script-shadow);
    line-height: 1;
    white-space: nowrap;
  }
  .signature-line {
    position: absolute;
    left: 120px;
    top: 372px;
    width: 460px;
    height: 0;
    border-top: 2px solid var(--ink);
  }
  .footer-band {
    position: absolute;
    left: 0;
    bottom: 0;
    width: 1100px;
    height: 220px;
  }
</style>
</head>
<body>
  <main class="canvas">
    <section class="compliment-slip">
      <div class="watercolour-wash" role="img" aria-label="Soft peach watercolour brush stroke"></div>
      <div class="brand-name">Dovetree</div>
      <h1 class="slip-title">With Compliments</h1>
      <div class="signature-line"></div>
      <svg class="footer-band" viewBox="0 0 1100 220" preserveAspectRatio="none" aria-hidden="true">
        <defs>
          <linearGradient id="band-fill" x1="0" y1="0" x2="0" y2="1">
            <stop offset="0" stop-color="var(--apricot-light)"/>
            <stop offset="0.25" stop-color="var(--apricot)"/>
            <stop offset="1" stop-color="var(--apricot)"/>
          </linearGradient>
        </defs>
        <path d="M0 168 C 380 150, 760 130, 920 70 C 1010 36, 1060 14, 1100 0 L 1100 220 L 0 220 Z" fill="url(#band-fill)"/>
      </svg>
    </section>
  </main>
</body>
</html>
```